Local Flower Farm Needs Business Card Design

I need business cards designed for a flower farm based in Eudora, Kansas.
Business Info:
We are a local cut flower farm located in Eudora, Kansas, founded by Corinne Haldwick. What started as a passion for agriculture and search for more joy in daily life has blossomed into a small business dedicated to providing the community with beautiful, fresh, and sustainable flowers. We specialize in local, seasonal blooms, ensuring that every petal reflects the care and dedication we pour into our craft. Our mission is to deliver the highest quality flowers directly to our customers through local farmers markets and to florists who share our commitment to sustainability. Join us in celebrating the beauty of nature, one bloom at a time!
Contact Details:
Corinne Haldwick
Owner
Phone 913-555-0147
Facebook: Rosalind Thorpe Gardens
Instagram: @RosalindThorpeGardens
Website: RosalindThorpeGardens.example
Target Market(s)
Wholesale to Florists and Direct to Consumer via Farmers Market
Industry/Entity Type
Florist, Farm
Contact Information for Business Card
Name, Contact Info, Logo
Look and feel
Each slider illustrates characteristics of the customer's brand and the style your logo design should communicate.

```html
<!DOCTYPE html>
<html lang="en">
<head>
<meta charset="utf-8">
<title>Rosalind Thorpe Gardens — Business Card</title>
<link href="https://fonts.googleapis.com/css2?family=Libre+Baskerville:wght@400;700&display=swap" rel="stylesheet">
<style>
  :root {
    --backdrop: #e4e5e5;
    --card: #ffffff;
    --ink: #1d3a38;
    --ink-soft: #2f3b3a;
    --strip-grey: #c7cbcb;
    --rule: #1d3a38;
  }
  * { box-sizing: border-box; margin: 0; padding: 0; }
  html, body {
    width: 1200px; height: 813px; overflow: hidden;
    background: var(--backdrop);
    font-family: "Libre Baskerville", Georgia, serif;
    color: var(--ink);
  }
  .stage {
    width: 1200px; height: 813px;
    display: flex; align-items: center; justify-content: center; gap: 48px;
  }
  .card {
    position: relative;
    width: 540px; height: 309px;
    background: var(--card);
    border-radius: 18px;
    overflow: hidden;
    box-shadow: 0 6px 18px rgba(0,0,0,.12);
  }
  /* front */
  .card-front { display: flex; align-items: center; justify-content: center; }
  .brand-seal {
    display: flex; align-items: center; justify-content: center;
    border: 2px solid var(--ink); border-radius: 50%;
    text-align: center; color: var(--ink);
    font-weight: 400; text-transform: uppercase; letter-spacing: .12em; line-height: 1.5;
  }
  .brand-seal--large { width: 220px; height: 220px; font-size: 19px; }
  .brand-seal--small { width: 148px; height: 148px; font-size: 13px; }
  /* back */
  .card-back .brand-seal { position: absolute; left: 28px; top: 72px; }
  .divider {
    position: absolute; left: 204px; top: 72px;
    width: 2px; height: 150px; background: var(--rule);
  }
  .contact { position: absolute; left: 222px; top: 78px; }
  .contact-name { font-size: 19px; font-weight: 700; color: var(--ink); }
  .contact-role { font-size: 12px; color: var(--ink-soft); margin: 4px 0 14px; }
  .contact-list { list-style: none; }
  .contact-list li {
    display: flex; align-items: center; gap: 6px;
    font-size: 13.5px; color: var(--ink-soft); line-height: 1.55;
  }
  .contact-list svg { width: 13px; height: 13px; flex: none; }
  .strip { position: absolute; left: 0; bottom: 0; width: 540px; height: 22px; }
</style>
</head>
<body>
<main class="stage">
  <section class="card card-front" aria-label="Card front">
    <div class="brand-seal brand-seal--large">Rosalind<br>Thorpe<br>Gardens</div>
  </section>

  <section class="card card-back" aria-label="Card back">
    <div class="brand-seal brand-seal--small">Rosalind<br>Thorpe<br>Gardens</div>
    <div class="divider"></div>
    <div class="contact">
      <p class="contact-name">Corinne Haldwick</p>
      <p class="contact-role">Owner</p>
      <ul class="contact-list">
        <li>
          <svg viewBox="0 0 16 16" aria-hidden="true"><path fill="#2f3b3a" d="M3.5 1.5l2.3 2.6-1.3 1.8c.9 1.9 2.6 3.6 4.6 4.6l1.8-1.3 2.6 2.3-1.4 2.2C7.5 13.6 2.4 8.5 1.3 3z"/></svg>
          913-555-0147
        </li>
        <li>
          <svg viewBox="0 0 16 16" aria-hidden="true"><g fill="none" stroke="#2f3b3a" stroke-width="1.4"><circle cx="8" cy="8" r="6.3"/><ellipse cx="8" cy="8" rx="2.8" ry="6.3"/><path d="M1.7 8h12.6"/></g></svg>
          RosalindThorpeGardens.example
        </li>
        <li>
          <svg viewBox="0 0 16 16" aria-hidden="true"><rect x="2" y="2" width="12" height="12" rx="2" fill="#2f3b3a"/></svg>
          Rosalind Thorpe Gardens
        </li>
        <li>
          <svg viewBox="0 0 16 16" aria-hidden="true"><rect x="2" y="2" width="12" height="12" rx="2" fill="#2f3b3a"/></svg>
          @RosalindThorpeGardens
        </li>
      </ul>
    </div>
    <svg class="strip" viewBox="0 0 540 22" preserveAspectRatio="none" aria-hidden="true">
      <rect x="0" y="0" width="540" height="22" fill="var(--strip-grey)"/>
      <polygon points="330,0 540,0 540,22 316,22" fill="var(--ink)"/>
    </svg>
  </section>
</main>
</body>
</html>
```